AI Discovery Workshop Presentation

We have a wireframe presentation with 43 slides (many with the same format) to be implemented in Powerpoint. We provide Corporate presentation in order to reuse template. Please, be creative and don't take the examples in the wireframe as literal. We also provide the following:
- Color palette
- lumacrest Logos
- Slide wireframe
- Flyer
- lumacrest Corporate Presentation. Please, use this as a general template.
You can find all the materials here:
https://files.brivoshare.net/folders/7QpZ2mTxR8vLkN4sYdW0aJe3Fu9HcBg?usp=sharing

```html
<!DOCTYPE html>
<html lang="en">
<head>
<meta charset="utf-8">
<title>AI Discovery Workshop – Slide Overview</title>
<link href="https://fonts.googleapis.com/css2?family=Outfit:wght@300;400;500;600;700;800&family=Space+Mono:wght@400;700&display=swap" rel="stylesheet">
<style>
:root{
  --purple:#8b1d8c;
  --magenta:#d23fc6;
  --teal:#2e9f98;
  --teal-light:#3fb8b0;
  --olive:#9b952a;
  --olive-light:#cfc64c;
  --navy:#1f2b37;
  --gray:#8a8c90;
  --ink:#1e1e24;
  --dark-bg:#221331;
  --yellow:#f5cf1a;
  --canvas:#e7e7ea;
}
*{box-sizing:border-box;margin:0;padding:0}
html,body{width:1200px;height:1052px;overflow:hidden}
body{background:radial-gradient(ellipse at center,#f4f4f6 0%,var(--canvas) 70%,#d9d9dd 100%);font-family:"Outfit",sans-serif;color:var(--ink);position:relative}
.deck{position:absolute;left:27px;top:30px;display:grid;grid-template-columns:repeat(4,279px);grid-auto-rows:157px;gap:9.6px 10px}
.slide{position:relative;overflow:hidden;background:#fff;box-shadow:0 2px 6px rgba(0,0,0,.12)}
.abs{position:absolute}
.light{background:linear-gradient(120deg,#e2f4f3 0%,#f7f7f9 45%,#f1e6f4 100%)}
.paper{background:linear-gradient(135deg,#f4f4f5,#e9e9ec)}
.dark{background:radial-gradient(ellipse at 70% 40%,#3b1d4d 0%,var(--dark-bg) 55%,#150c1e 100%);color:#fff}
.photo{position:absolute}
.h{font-weight:700;line-height:1.02;letter-spacing:-.2px}
.p{font-size:5px;line-height:1.35;font-weight:300}
.spaced{font-weight:500;letter-spacing:2px;text-transform:uppercase}
.white{color:#fff}.purple{color:var(--purple)}.teal{color:var(--teal)}.magenta{color:var(--magenta)}.olive{color:var(--olive-light)}.navy{color:var(--navy)}
.brand{font-weight:700;display:flex;align-items:center;gap:3px}
.brand i{display:block;width:7px;height:7px;background:var(--teal)}
.circle{position:absolute;border-radius:50%;display:flex;flex-direction:column;align-items:center;justify-content:center;text-align:center;line-height:1.05}
.circle b{font-weight:600;font-size:9px}.circle span{font-size:6px;font-weight:400}
.tile{position:absolute;color:#fff;font-size:5.6px;font-weight:500;line-height:1.15;padding:4px 5px;display:flex;flex-direction:column;justify-content:flex-end}
.t-purple{background:var(--purple)}.t-teal{background:var(--teal)}.t-olive{background:var(--olive)}.t-navy{background:var(--navy)}.t-gray{background:var(--gray)}
.ring{position:absolute}
.ring text{font-family:"Outfit",sans-serif;font-weight:700;fill:#fff}
.bubble{position:absolute;border-radius:5px;font-size:3.6px;line-height:1.3;padding:4px 5px}
.bubble b{font-weight:600;display:block}
.b-gray{background:#ededf0;color:#333;box-shadow:0 1px 3px rgba(0,0,0,.15)}
.b-teal{background:var(--teal-light);color:#fff}
.b-purple{background:var(--purple);color:#fff}
.bullets{list-style:none;font-size:5px;color:#555;line-height:1.9}
.bullets li::before{content:"";display:inline-block;width:5px;height:4px;margin-right:3px;background:linear-gradient(90deg,var(--teal) 0 30%,transparent 30% 40%,var(--teal) 40% 65%,transparent 65% 75%,var(--teal) 75%)}
.node{position:absolute;font-size:5px;line-height:1.2;color:#555}
.node b{font-weight:600;color:var(--ink);display:block;font-size:5.6px}
.col-box{position:absolute;border:1px solid #9fd4d0;border-radius:2px}
.small{font-size:4px;line-height:1.3;color:#555}
</style>
</head>
<body>
<svg width="0" height="0" style="position:absolute" aria-hidden="true">
  <defs>
    <linearGradient id="ringStroke" x1="0" y1="0" x2="1" y2="1">
      <stop offset="0" stop-color="#ff9a3c"/>
      <stop offset=".5" stop-color="#e0408a"/>
      <stop offset="1" stop-color="#ff9a3c"/>
    </linearGradient>
    <radialGradient id="ringFill" cx=".5" cy=".5" r=".5">
      <stop offset=".7" stop-color="#120a18"/>
      <stop offset="1" stop-color="#3a1c3c"/>
    </radialGradient>
  </defs>
</svg>

<main class="deck">

  <!-- 1 Title -->
  <section class="slide">
    <div class="photo" role="img" aria-label="Photo of a person working on a laptop beside a humanoid robot, dark blue and purple tones" style="inset:0;background:linear-gradient(110deg,#122a57 0%,#1e2f6d 40%,#2c2460 70%,#5a2a6e 100%)"></div>
    <div class="abs brand white" style="left:24px;top:13px;font-size:15px"><i></i>lumacrest</div>
    <div class="abs h white" style="left:24px;top:52px;font-size:22px">AI Discovery<br><span style="margin-left:18px">Workshop</span></div>
    <div class="abs" style="left:24px;top:117px;width:84px;height:24px;background:rgba(46,159,152,.35);border-radius:2px;padding:4px 5px;font-size:5.6px;line-height:1.4">
      <div style="color:#57d3c9">Presented By</div><div class="white">R. Alan Moreno | 2026</div>
    </div>
  </section>

  <!-- 2 Introductions -->
  <section class="slide">
    <div class="abs h navy" style="left:18px;top:33px;font-size:18px;font-weight:800">INTRO-<br>DUCTIONS</div>
    <div class="photo" role="img" aria-label="Photo of a white humanoid robot with glowing data screens" style="left:128px;top:14px;width:138px;height:106px;border-radius:5px;background:linear-gradient(135deg,#3a2c22,#19475a 45%,#1d9ea8)"></div>
    <div class="abs" style="left:33px;top:87px;width:133px;height:56px;background:var(--purple);border-radius:2px;padding:5px 7px;color:#fff;font-size:5.6px;font-weight:600;line-height:1.15">
      <div style="border-bottom:.5px solid rgba(255,255,255,.4);padding-bottom:2px">Name</div>
      <div style="border-bottom:.5px solid rgba(255,255,255,.4);padding:2px 0">Department</div>
      <div style="border-bottom:.5px solid rgba(255,255,255,.4);padding:2px 0">ROL</div>
      <div style="padding-top:2px">Workshp<br>Expectations</div>
    </div>
  </section>

  <!-- 3 About us -->
  <section class="slide">
    <div class="photo" role="img" aria-label="Digital illustration of glowing data waves, charts and cloud icons on a dark blue background" style="inset:0;background:radial-gradient(ellipse at 30% 40%,#1e4aa8 0%,#102660 45%,#0a1436 100%)"></div>
    <div class="abs white" style="left:40px;right:40px;top:33px;text-align:center">
      <div class="spaced" style="font-size:8px;font-weight:400;letter-spacing:2.5px">About us</div>
      <div class="h" style="font-size:11px;margin-top:2px">Data Analytics and AI<br>for Nonconformists</div>
      <div class="p" style="margin:4px auto 0;width:105px">We are a leading Professional Services company specialized in the design and implementation of cutting edge technologies in Cloud Data Analytics &amp; AI.</div>
    </div>
  </section>

  <!-- 4 About the workshop -->
  <section class="slide light">
    <div class="abs h" style="left:19px;top:48px;font-size:15px;color:#3b1d5a">About The<br><span class="purple">Workshop</span></div>
    <div class="abs p" style="left:19px;top:86px;width:80px;color:#444">The objective of this workshop is for you to discover feasible and high-impact AI use cases.</div>
    <div class="abs brand navy" style="left:142px;top:67px;font-size:15px"><i></i>lumacrest</div>
    <div class="abs" style="left:123px;top:43px;font-size:7px;line-height:1.1;font-weight:500">You,<br>Not Us</div>
    <div class="abs" style="left:215px;top:43px;font-size:7px;line-height:1.1;font-weight:500">High<br>Impact</div>
    <div class="abs" style="left:164px;top:104px;font-size:7px;line-height:1.1;font-weight:500">Feasible,<br>No Impossible</div>
    <svg class="abs" style="left:0;top:0" width="279" height="157" aria-hidden="true" fill="none" stroke="#666" stroke-width=".5">
      <path d="M148 46 H170 V60"/><path d="M213 46 H204 V55"/><path d="M207 92 V104 H200"/>
      <circle cx="170" cy="60" r="1" fill="#666"/><circle cx="204" cy="55" r="1" fill="#666"/>
    </svg>
  </section>

  <!-- 5 Agenda -->
  <section class="slide paper">
    <div class="abs h purple" style="left:19px;top:63px;font-size:24px">Agenda</div>
    <div class="circle" style="left:131px;top:23px;width:50px;height:50px;background:#fff;border:2px solid var(--teal)"><b>Inspire</b><span>60 Mins</span></div>
    <div class="circle white" style="left:199px;top:36px;width:51px;height:51px;background:var(--navy);border:2px solid var(--teal)"><b>Discover</b><span>60 Mins</span></div>
    <div class="circle white" style="left:153px;top:88px;width:52px;height:52px;background:var(--teal);border:2px solid var(--navy)"><b>Priortize</b><span>90 Mins</span></div>
    <svg class="abs" style="left:0;top:0" width="279" height="157" aria-hidden="true" fill="none" stroke="#333" stroke-width=".7">
      <path d="M185 33 Q193 29 199 38"/><path d="M196 36 l3 2 l0-3.5"/>
      <path d="M220 92 Q220 100 210 104"/><path d="M212 101 l-2 3 l3.5 .5"/>
    </svg>
  </section>

  <!-- 6 Agenda (Inspire active) -->
  <section class="slide paper">
    <div class="abs h purple" style="left:19px;top:63px;font-size:24px">Agenda</div>
    <div class="circle white" style="left:126px;top:17px;width:58px;height:58px;background:var(--teal-light)"><b style="font-size:11px">Inspire</b><span style="font-size:8px">60 Mins</span></div>
    <div class="circle" style="left:200px;top:40px;width:44px;height:44px;background:#fff;border:1.5px solid var(--teal)"><b style="font-size:7.5px">Discover</b><span>60 Mins</span></div>
    <div class="circle" style="left:163px;top:93px;width:45px;height:45px;background:#fff;border:1.5px solid var(--navy)"><b style="font-size:7.5px">Priortize</b><span>90 Mins</span></div>
    <svg class="abs" style="left:0;top:0" width="279" height="157" aria-hidden="true" fill="none" stroke="#333" stroke-width=".7">
      <path d="M188 36 Q196 32 201 40"/><path d="M198 38 l3 2 l0-3.5"/>
      <path d="M219 89 Q220 97 211 101"/><path d="M213 98 l-2 3 l3.5 .5"/>
    </svg>
  </section>

  <!-- 7 Artificial Intelligence -->
  <section class="slide dark">
    <div class="abs h" style="left:18px;top:42px;font-size:16px">Artificial<br><span class="magenta">Intelligence</span></div>
    <div class="abs p" style="left:18px;top:86px;width:88px;opacity:.85">"It is the general field of computer science dedicated to creating machines that can simulate human intelligence"</div>
    <svg class="ring" style="left:146px;top:20px" width="108" height="108" aria-hidden="true">
      <circle cx="54" cy="54" r="51" fill="url(#ringFill)" stroke="url(#ringStroke)" stroke-width="3"/>
      <text x="54" y="62" text-anchor="middle" font-size="22">AI</text>
    </svg>
  </section>

  <!-- 8 Machine Learning -->
  <section class="slide dark">
    <div class="abs h" style="left:18px;top:42px;font-size:16px">Machine<br><span style="color:var(--teal-light)">Learning</span></div>
    <div class="abs p" style="left:18px;top:86px;width:115px;opacity:.85">Machine learning is a subfield of artificial intelligence that focuses on enabling machines to learn from data using algorithms without being explicitly programmed for each task</div>
    <svg class="ring" style="left:144px;top:20px" width="114" height="114" aria-hidden="true">
      <circle cx="57" cy="57" r="54" fill="url(#ringFill)" stroke="url(#ringStroke)" stroke-width="3"/>
      <circle cx="57" cy="72" r="32" fill="url(#ringFill)" stroke="url(#ringStroke)" stroke-width="2.5"/>
      <text x="57" y="32" text-anchor="middle" font-size="17">AI</text>
      <text x="57" y="79" text-anchor="middle" font-size="17">ML</text>
    </svg>
  </section>

  <!-- 9 ML examples -->
  <section class="slide light">
    <div class="abs h" style="left:18px;top:54px;font-size:14px">Machine<br><span class="teal">Learning<br>Examples</span></div>
    <div class="tile t-purple" style="left:93px;top:34px;width:56px;height:43px">Demand<br>Prediction</div>
    <div class="tile t-gray" style="left:93px;top:79px;width:56px;height:43px">Recommendation<br>Engine</div>
    <div class="tile t-navy" style="left:151px;top:34px;width:56px;height:88px;justify-content:flex-start;text-align:center;padding-top:20px">Customer<br>Segment</div>
    <div class="tile t-teal" style="left:209px;top:34px;width:56px;height:43px">Fraud<br>Detection</div>
    <div class="tile t-olive" style="left:209px;top:79px;width:56px;height:43px">Employee<br>Attrition, Churn</div>
  </section>

  <!-- 10 Cat or dog -->
  <section class="slide">
    <div class="photo" role="img" aria-label="Hand-drawn sketch on yellow asking 'Is this a cat or dog?' with a photo of a pet in a basket feeding a deep neural network diagram with input, activated neurons and output layers" style="inset:0;background:var(--yellow)"></div>
  </section>

  <!-- 11 Foundational Models -->
  <section class="slide dark">
    <div class="abs h" style="left:18px;top:42px;font-size:16px"><span class="magenta">Foundational</span><br>Models</div>
    <div class="abs p" style="left:18px;top:86px;width:100px;opacity:.85">A foundational model is a large-scale ML model, trained on vast amounts of data, that serves as the underlying platform for <b style="font-weight:600">Generative AI (GenAI)</b> to create new and original content.</div>
    <svg class="ring" style="left:144px;top:14px" width="114" height="130" aria-hidden="true">
      <circle cx="57" cy="62" r="55" fill="url(#ringFill)" stroke="url(#ringStroke)" stroke-width="3"/>
      <circle cx="57" cy="80" r="37" fill="url(#ringFill)" stroke="url(#ringStroke)" stroke-width="2.5"/>
      <circle cx="57" cy="96" r="20" fill="url(#ringFill)" stroke="url(#ringStroke)" stroke-width="2"/>
      <text x="57" y="32" text-anchor="middle" font-size="16">AI</text>
      <text x="57" y="68" text-anchor="middle" font-size="14">ML</text>
      <text x="57" y="102" text-anchor="middle" font-size="14">FM</text>
    </svg>
  </section>

  <!-- 12 FM examples -->
  <section class="slide light">
    <div class="abs h" style="left:17px;top:66px;font-size:11.5px"><span class="purple">Foundational</span><br>Models<br>Examples</div>
    <div class="tile t-teal" style="left:93px;top:34px;width:56px;height:43px">Face<br>Recognition</div>
    <div class="tile t-olive" style="left:93px;top:79px;width:56px;height:43px">Video, Image<br>Detection</div>
    <div class="tile t-navy" style="left:151px;top:34px;width:56px;height:43px;justify-content:flex-start"><span style="font-size:5.6px">Video<br>Generation</span><span style="font-size:3.4px;margin-top:2px;font-weight:300">https://clipvault.io/<br>watch?v=Q7rPzL2</span></div>
    <div class="photo" role="img" aria-label="Laptop showing a generated video frame" style="left:151px;top:79px;width:62px;height:46px;background:linear-gradient(160deg,#1b1b22,#7b7d84);border-radius:2px"></div>
    <div class="tile t-purple" style="left:209px;top:34px;width:56px;height:43px">Product<br>Design</div>
    <div class="tile t-gray" style="left:209px;top:79px;width:56px;height:43px">Marketing<br>Content</div>
  </section>

  <!-- 13 LLM -->
  <section class="slide dark">
    <div class="abs h" style="left:18px;top:22px;font-size:16px">Large<br><span class="olive">Language</span><br>Models</div>
    <div class="abs p" style="left:18px;top:80px;width:100px;opacity:.85">They are a type of foundational models capable of understanding, generating, translating, and summarizing human language with impressive fluency. This opens a hole new paradigm.</div>
    <svg class="ring" style="left:161px;top:10px" width="106" height="140" aria-hidden="true">
      <circle cx="53" cy="70" r="50" fill="url(#ringFill)" stroke="url(#ringStroke)" stroke-width="2.5"/>
      <circle cx="53" cy="86" r="34" fill="url(#ringFill)" stroke="url(#ringStroke)" stroke-width="2.2"/>
      <circle cx="53" cy="99" r="21" fill="url(#ringFill)" stroke="url(#ringStroke)" stroke-width="2"/>
      <circle cx="53" cy="108" r="12" fill="url(#ringFill)" stroke="url(#ringStroke)" stroke-width="1.6"/>
      <text x="53" y="39" text-anchor="middle" font-size="11">AI</text>
      <text x="53" y="61" text-anchor="middle" font-size="11">ML</text>
      <text x="53" y="84" text-anchor="middle" font-size="11">FM</text>
      <text x="53" y="112" text-anchor="middle" font-size="10">LLM</text>
    </svg>
  </section>

  <!-- 14 LLM + RAG -->
  <section class="slide">
    <div class="abs h" style="left:15px;top:20px;font-size:10px;line-height:1.15"><span class="teal">Large Language<br>Models</span> (LLM) +<br><span class="purple">Retrieva Augmented<br>Generation</span> (RAG)</div>
    <ul class="abs bullets" style="left:15px;top:75px">
      <li>Improved Accuracy</li><li>Access to Up-to-Date Information</li><li>Use of Proprietary/Private Data</li><li>Transparency and Auditability</li><li>Cost-Effectiveness vs Training</li>
    </ul>
    <svg class="abs" style="left:0;top:0" width="279" height="157" aria-hidden="true">
      <g fill="none" stroke="#555" stroke-width=".6">
        <path d="M146 42 V32 H168"/><path d="M165 30.5 l3 1.5 l-3 1.5"/>
        <path d="M213 32 H228 V44"/><path d="M226.5 41 l1.5 3 l1.5-3"/>
        <path d="M220 70 H176"/><path d="M179 68.5 l-3 1.5 l3 1.5"/>
        <path d="M172 70 H160"/><path d="M163 68.5 l-3 1.5 l3 1.5"/>
        <path d="M172 60 V80"/><path d="M170.5 63 l1.5-3 l1.5 3"/>
        <path d="M176 60 V80"/><path d="M174.5 77 l1.5 3 l1.5-3"/>
      </g>
      <rect x="160" y="36" width="18" height="15" rx="1.5" fill="#f3b63c"/>
      <rect x="160" y="33" width="8" height="4" rx="1" fill="#e19a22"/>
      <circle cx="146" cy="50" r="4.5" fill="#111"/><path d="M138 64 a8 7 0 0 1 16 0 z" fill="#111"/>
      <rect x="218" y="53" width="22" height="16" rx="1.5" fill="#4a4a4a"/>
      <rect x="221" y="56" width="16" height="1.5" fill="#8a8a8a"/><rect x="221" y="60" width="16" height="1.5" fill="#8a8a8a"/><rect x="221" y="64" width="16" height="1.5" fill="#8a8a8a"/>
      <rect x="166" y="93" width="18" height="20" fill="#7a5c4a"/><ellipse cx="175" cy="93" rx="9" ry="3" fill="#9b7a66"/><ellipse cx="175" cy="113" rx="9" ry="3" fill="#5e4436"/>
    </svg>
    <div class="node" style="left:161px;top:54px;font-size:5px">Retrieval</div>
    <div class="node" style="left:132px;top:67px;font-size:5px">User Prompt</div>
    <div class="node" style="left:158px;top:82px;font-size:5px;text-align:center">Knowledge<br>Base</div>
    <div class="node" style="left:225px;top:73px;font-size:5px">LLM</div>
  </section>

  <!-- 15 FM examples 2 -->
  <section class="slide light">
    <div class="abs h" style="left:17px;top:66px;font-size:11.5px"><span class="purple">Foundational</span><br>Models<br>Examples</div>
    <div class="tile t-gray" style="left:93px;top:34px;width:56px;height:43px">Customer<br>Assistant</div>
    <div class="tile t-olive" style="left:93px;top:79px;width:56px;height:43px">Employee HR<br>Assistant</div>
    <div class="tile t-navy" style="left:151px;top:34px;width:56px;height:88px;justify-content:flex-start;text-align:center;padding-top:20px">Semantic<br>Searh</div>
    <div class="tile t-purple" style="left:209px;top:34px;width:56px;height:43px">Natural Language<br>Reporting</div>
    <div class="tile t-teal" style="left:209px;top:79px;width:56px;height:43px">Sales &amp; Marketing<br>Support</div>
  </section>

  <!-- 16 LLM + RAG: E-commerce -->
  <section class="slide">
    <div class="abs spaced" style="left:17px;top:21px;font-size:6px;letter-spacing:1.6px">LLM + RAG Examples:</div>
    <div class="abs h teal" style="left:17px;top:30px;font-size:11px">E-commerce<br>Fashion Recommender</div>
    <div class="bubble b-gray" style="left:154px;top:14px;width:111px;height:37px"><b>Client's Request:</b>I'm looking for a t-shirt similar to this photo, but I'd like it to go well with the pants I bought last month. Can you tell me if it is available in my size at the store closest to my workplace?</div>
    <div class="bubble b-purple" style="left:64px;top:62px;width:193px;height:76px;font-size:3.5px">
      <b>LLM + RAG Response:</b>We've found a few t-shirts we think you'll love. Based on the photo and your 'Classic Fit' pants, we recommend these two options that match your style.<br>
      <b>Organic Cotton T-shirt – 'Urban Flow' Model:</b> Available in your size M at our store on Main Street (just 5 minutes from your work). It pairs perfectly with dark jeans. [Link to online product + photo with pants + t-shirt]<br>
      <b>Premium Linen T-shirt – 'Coastal Breeze' Model:</b> Available in your size M at our store on Central Square (about 10 minutes from your workplace). Ideal for a casual-chic look. [Link to online product + photo with pants + t-shirt]
    </div>
  </section>

  <!-- 17 E-commerce data map -->
  <section class="slide">
    <div class="abs" style="left:0;right:0;top:54px;text-align:center">
      <div class="spaced" style="font-size:6px;letter-spacing:1.6px">LLM + RAG Examples:</div>
      <div class="h" style="font-size:11px;margin-top:2px"><span class="teal">E-commerce</span><br><span class="teal">Fashion</span> Recommender</div>
    </div>
    <div class="node" style="left:114px;top:16px;width:60px"><b>Product catalog</b>Images &amp; descriptions to find "visually similar t-shirts.</div>
    <div class="node" style="left:28px;top:46px;width:50px"><b>Customer Data</b>City, preferences, etc.</div>
    <div class="node" style="left:209px;top:34px;width:50px"><b>Previous T-Shirt Purchases</b>To determine the customer's size.</div>
    <div class="node" style="left:28px;top:95px;width:52px"><b>Previous Pants Purchases</b>Images &amp; descriptions to find "visually similar complements to the t-shirt.</div>
    <div class="node" style="left:104px;top:104px;width:74px"><b>Knowledge Graph Data</b>Relationships between clothing items (styles, colors, brands, fashion attributes) and links like "matches with," "is in the style of," "is from the brand."</div>
    <div class="node" style="left:191px;top:95px;width:66px"><b>Article Stock by Store &amp; Location</b>To find a "store near the city center" that has the selected t-shirt in the customer's size.</div>
    <svg class="abs" style="left:0;top:0" width="279" height="157" aria-hidden="true" fill="none" stroke="#555" stroke-width=".6">
      <path d="M53 63 V67 H76"/><path d="M144 45 V52"/><path d="M227 58 V63 H206"/>
      <path d="M53 94 V89 H78"/><path d="M144 98 V103"/><path d="M227 94 V89 H200"/>
    </svg>
  </section>

  <!-- 18 Employee assistant chat -->
  <section class="slide">
    <div class="abs spaced" style="left:17px;top:30px;font-size:6px;letter-spacing:1.6px;line-height:1.2">LLM + RAG<br>Examples:</div>
    <div class="abs h purple" style="left:17px;top:46px;font-size:12px">Employee<br>Assistant</div>
    <div class="bubble b-gray" style="left:164px;top:14px;width:101px;height:22px"><b>Employee's Request:</b>Hi, I'd like to know how many vacation days I have</div>
    <div class="bubble b-teal" style="left:87px;top:40px;width:117px;height:37px"><b>LLM + RAG Response:</b>Hi Juan, since you joined the company on April 5th of this year, you currently have 7 vacation days</div>
    <div class="bubble b-gray" style="left:160px;top:95px;width:100px;height:22px"><b>Employee's Request:</b>Great. How can I request 3 days for next week?</div>
    <div class="bubble b-teal" style="left:50px;top:92px;width:120px;height:41px"><b>LLM + RAG Response:</b>You can see the vacation request policy by clicking here. If you'd like to submit a request, you can fill out this form and your manager will receive it for approval.</div>
  </section>

  <!-- 19 Employee assistant flow -->
  <section class="slide">
    <div class="photo" role="img" aria-label="Illustration of a laptop with a magnifying glass over colorful charts" style="left:200px;top:5px;width:70px;height:52px;border-radius:4px;background:linear-gradient(135deg,#7bc6e8,#b06ad6 55%,#f08aa0)"></div>
    <div class="abs" style="left:0;right:0;top:36px;text-align:center">
      <div class="spaced" style="font-size:6px;letter-spacing:1.6px">LLM + RAG Examples:</div>
      <div class="h purple" style="font-size:12px;margin-top:2px">Employee Assistant</div>
    </div>
    <svg class="abs" style="left:0;top:0" width="279" height="157" aria-hidden="true">
      <g fill="#2e9f98">
        <rect x="56" y="81" width="14" height="4" rx="2"/><rect x="56" y="86" width="14" height="4" rx="2"/><rect x="56" y="91" width="14" height="4" rx="2"/>
      </g>
      <rect x="127" y="80" width="11" height="14" rx="1" fill="#9b952a"/><circle cx="137" cy="92" r="3.5" fill="#2e9f98"/>
      <g fill="#8b1d8c"><circle cx="197" cy="83" r="2.5"/><circle cx="207" cy="83" r="2.5"/><rect x="194" y="88" width="16" height="6" rx="1"/></g>
      <g fill="#8b1d8c"><circle cx="86" cy="88" r="1.3"/><circle cx="112" cy="88" r="1.3"/><circle cx="156" cy="88" r="1.3"/><circle cx="184" cy="88" r="1.3"/></g>
      <g stroke="#2e9f98" stroke-width=".6"><path d="M86 88 H112"/><path d="M156 88 H184"/></g>
    </svg>
    <div class="node" style="left:42px;top:100px;font-size:7px;color:var(--ink)">HR Database</div>
    <div class="node" style="left:110px;top:100px;font-size:7px;color:var(--ink)">Vacation Policy</div>
    <div class="node" style="left:182px;top:100px;font-size:7px;color:var(--ink);line-height:1.05">Vacation Request<br>Process</div>
  </section>

  <!-- 20 AI Agents -->
  <section class="slide">
    <div class="photo" role="img" aria-label="Photo of a businessman in a suit touching a glowing holographic interface, dark blue tones" style="inset:0;background:radial-gradient(ellipse at 72% 55%,#1f5d8f 0%,#0e1d33 45%,#05080f 100%)"></div>
    <div class="abs h white" style="left:17px;top:42px;font-size:18px">AI Agents</div>
    <div class="abs p white" style="left:17px;top:66px;width:100px;font-size:5.4px">"An AI Agent is an application based on LLMs that can perceive its environment, make decisions, and act to achieve specific goals."</div>
  </section>

  <!-- 21 Agentic AI -->
  <section class="slide">
    <div class="photo" role="img" aria-label="Photo of a man in glasses reaching toward a glowing holographic model, dark blue tones" style="inset:0;background:radial-gradient(ellipse at 65% 60%,#1e6ea0 0%,#0e1c30 45%,#04070d 100%)"></div>
    <div class="abs white" style="left:17px;top:31px">
      <div class="spaced" style="font-size:9px;letter-spacing:2.4px">What is</div>
      <div class="h" style="font-size:18px;margin-top:1px">Agentic AI</div>
    </div>
    <div class="abs p white" style="left:17px;top:69px;width:100px;font-size:5.4px">An Agentic AI is a <span class="magenta">goal-oriented</span> system, comprising one or more agents that leverages understanding of <span style="color:#4fc3f7">context</span>, to drive <span style="color:#4fc3f7">conversations</span>, performs <span style="color:#f5cf1a">actions</span> and manage short and long-term workflows.</div>
  </section>

  <!-- 22 AI Agent HR -->
  <section class="slide">
    <div class="abs h" style="left:15px;top:63px;font-size:12px">AI Agent<br><span class="teal" style="font-size:7.5px;font-weight:500">Examples, HR<br>Request Agent</span></div>
    <div class="node" style="left:82px;top:20px;font-size:6px;color:var(--ink)">Human Capital</div>
    <div class="node" style="left:169px;top:13px;font-size:6px;color:var(--ink);text-align:center">Functional<br>Workflow</div>
    <div class="node" style="left:226px;top:20px;font-size:6px;color:var(--ink)">IT Assests</div>
    <div class="col-box" style="left:82px;top:33px;width:73px;height:112px;padding:3px 4px">
      <div class="purple" style="font-size:6.5px;font-weight:500">Human</div>
      <div class="small" style="margin-top:2px"><b>User</b><br>I'd like to request some vacation time.</div>
      <div class="small" style="margin:3px 0 0 16px">You have 15 days available. How many days &amp; when?</div>
      <div class="small" style="margin-top:3px"><b>User</b><br>I'd like 5 days starting on August 1</div>
      <div class="small" style="margin-top:4px"><b>Manager</b><br>I approve this request</div>
      <div class="small" style="margin:3px 0 0 16px">Your request went through successfully</div>
    </div>
    <div class="col-box" style="left:165px;top:33px;width:42px;height:112px;padding:3px;text-align:center;font-size:6px;line-height:1.1">
      <div class="teal" style="font-weight:500">AI Agents</div>
      <div class="olive" style="color:var(--olive);margin-top:7px">Goal</div>
      <div style="color:var(--olive);margin-top:7px">No days<br>call</div>
      <div style="color:var(--olive);margin-top:7px">No days<br>call</div>
      <div style="color:var(--olive);margin-top:6px">Iteration<br>Summary</div>
      <div style="margin-top:4px">Vacation<br>Request</div>
    </div>
    <div class="abs small" style="left:212px;top:35px;width:56px;text-align:center;color:#999;line-height:1.25">
      <b style="color:#333">RAG</b><br>Process Instruction Tools, data &amp; rules<br><br><b style="color:#333">API</b><br>HCM (Information)<br><br><b style="color:#333">API</b><br>Email to Manager<br><br><b style="color:#333">API</b><br>Store in long term memory<br><br><b style="color:#333">API</b><br>HCM (Transaction)
    </div>
  </section>

  <!-- 23 Customer support flow -->
  <section class="slide">
    <div class="abs h" style="left:75px;top:13px;font-size:12px">AI Agent</div>
    <div class="abs purple" style="left:134px;top:11px;font-size:7px;font-weight:500;line-height:1.05">Examples. Customer<br>Support Agent</div>
    <div class="abs" style="left:11px;top:32px;width:18px;height:114px;background:var(--teal-light);display:flex;align-items:center;justify-content:center"><span style="transform:rotate(-90deg);color:#fff;font-size:9px;font-weight:600;white-space:nowrap">Customer</span></div>
    <div class="abs" style="left:163px;top:32px;width:18px;height:114px;background:var(--purple);display:flex;align-items:center;justify-content:center"><span style="transform:rotate(-90deg);color:#fff;font-size:9px;font-weight:600;white-space:nowrap">AI Agent</span></div>
    <div class="abs small" style="left:33px;top:34px;width:93px;line-height:1.3;font-size:3.7px">
      Hi, my package arrived, but it contains the wrong product.<br>
      <div style="text-align:right;margin-top:2px">Understood. May I have the product number?<br>You'll find it listed on the invoice.</div>
      <div style="margin-top:2px">Sure!. It is 3447148T</div>
      <div style="text-align:right;margin-top:2px">I've confirmed that the incorrect product was sent to you. Please accept our apologies for this error. We're ready to dispatch the correct item immediately. Would you like us to proceed?</div>
      <div style="margin-top:2px">Yes, please!</div>
      <div style="text-align:right;margin-top:2px">Confirmed! Your new shipment will arrive within 48 hours. Your return package is ready. Anything else I can assist you with?</div>
      <div style="margin-top:2px">No, thanks. This is all.</div>
      <div style="text-align:right;margin-top:1px">OK. Have a great day!</div>
    </div>
    <div class="abs small" style="left:186px;top:34px;width:85px;line-height:1.3;font-size:3.7px">
      Check Customer Purchase Order<div class="purple" style="text-align:right;font-size:5px;font-weight:500">→ Sales System</div>
      <div style="margin-top:10px">Check Product Sent</div><div style="margin-top:3px">Check Product Availability</div><div style="margin-top:3px">Process Product Shipment</div>
      <div class="purple" style="text-align:right;font-size:5px;font-weight:500">→ Logistics System</div>
      <div style="margin-top:10px">Register issue for later analysis</div>
      <div class="purple" style="text-align:right;font-size:5px;font-weight:500">→ Quality System</div>
    </div>
    <svg class="abs" style="left:0;top:0" width="279" height="157" aria-hidden="true" stroke="#2e9f98" stroke-width=".5" fill="none">
      <path d="M129 37 H160"/><path d="M160 48 H129"/><path d="M129 58 H160"/><path d="M160 70 H129"/><path d="M129 82 H160"/><path d="M160 94 H129"/><path d="M129 104 H160"/><path d="M160 115 H129"/>
    </svg>
  </section>

  <!-- 24 AI Agent dimensions -->
  <section class="slide">
    <div class="abs" style="left:0;right:0;top:12px;text-align:center">
      <div class="h" style="font-size:12px">AI Agent</div>
      <div class="teal" style="font-size:7px;font-weight:500;margin-top:2px">Examples, Customer Support Agent</div>
    </div>
    <div class="abs small" style="left:14px;top:52px;width:52px;font-size:3.8px">
      <div class="purple" style="font-size:6px;font-weight:500;margin-bottom:2px">Goal</div>
      Reduce incident volume and enhance customer satisfaction by resolving issues before they're reported, or by offering relevant self-service precisely when needed.
    </div>
    <div class="abs small" style="left:76px;top:52px;width:54px;font-size:3.8px;border-right:.5px solid #9fd4d0;height:85px">
      <div class="purple" style="font-size:6px;font-weight:500;margin-bottom:2px">Perceptions</div>
      &gt; User behavior on digital platforms Product/service data<br><br>&gt; Customer history<br><br>&gt; Support knowledge base<br><br>&gt; Customer sentiment<br><br>&gt; Internal system alerts
    </div>
    <div class="abs small" style="left:141px;top:52px;width:58px;font-size:3.8px;border-right:.5px solid #9fd4d0;height:85px">
      <div class="purple" style="font-size:6px;font-weight:500;margin-bottom:2px">Decisions</div>
      &gt; Identify signs of frustration/problems.<br><br>&gt; Predict customer intent. Decide on proactive intervention.<br><br>&gt; Choose the most relevant resource.<br><br>&gt; Decide when to escalate.<br><br>&gt; Identify signals of frustration.
    </div>
    <div class="abs small" style="left:209px;top:52px;width:58px;font-size:3.8px">
      <div class="navy" style="font-size:6px;font-weight:500;margin-bottom:2px">Actions</div>
      &gt; Show contextual pop-ups.<br><br>&gt; Suggest knowledge base articles.<br><br>&gt; Activate a self-service chatbot.<br><br>&gt; Send personalized push notifications.<br><br>&gt; Preliminarily open a support ticket.<br><br>&gt; Offer a call or chat with a human agent.
    </div>
  </section>

</main>
</body>
</html>
```